Landingpage design

We need a landingpage for a Chatterloom add campaign. We sell socks made of bamboo in super quality. Our customers loves us, and we have a 5 heart rating at scorevane.com.

We want to create a add campaign targeted new customers, and the offer is that they can buy 1 pair of bamboo socks as a test, for only 20 DKK (2,7 Euro) including shipment. Our webpage is www.tuvelo.dk, landingpage should be built i Kyvio, a wysiwyg editor. based on their template. like:
https://tuvelo.pemlorsite.com/13844-sales-page
https://tuvelo.pemlorsite.com/13696-sales-page
https://tuvelo.pemlorsite.com/13845-sales-page

You don't have to follow the templates 100% if you have better ideas. We have an account for snapvaultly, so please get stockphotos from here.

Bamboo socks has a lot of great selling points, you can see a good desciption here:
https://feltrano.com/us/why-bamboo

We expect you to have experience in landingpage design, and expect to end up with 2 landingpages we can splittest on.

This is the first of a number of landingpages we need in the future, so for the right person there will be plenty of more work.

Target Market(s)

Denmark

Industry/Entity Type

E-Commerce

Number of Pages Required

2 page

Colors

Designer to choose colors to be used in the design.

Requirements
Must have
• A great selling page, showing all the great things with bamboo socks. It should be supplied with good packshots from snapvaultly.com

```html
<!DOCTYPE html>
<html lang="en">
<head>
<meta charset="utf-8">
<title>Tuvelo – Bamboo Socks</title>
<link href="https://fonts.googleapis.com/css2?family=Roboto:wght@400;500;700&display=swap" rel="stylesheet">
<style>
:root{
  --green:#3bb083;
  --green-dark:#2f9d73;
  --ink:#3a3a3a;
  --muted:#8a8a8a;
  --hero-bg:#e3e3e3;
  --white:#ffffff;
  --band:#e8f0e4;
  --line:#e6e6e6;
}
*{box-sizing:border-box;margin:0;padding:0}
html,body{width:1200px;height:2338px;overflow:hidden}
body{font-family:"Roboto",Arial,sans-serif;color:var(--ink);background:var(--white);position:relative}

/* header */
.site-header{position:absolute;left:0;top:0;width:1200px;height:70px;background:var(--white);border-bottom:1px solid var(--line)}
.brand{position:absolute;left:134px;top:17px;display:flex;align-items:center;gap:12px}
.brand-square{width:36px;height:36px;border:3px solid var(--ink)}
.brand-name{font-weight:700;font-size:18px;letter-spacing:1px;color:var(--ink)}
.brand-tagline{font-size:14px;font-weight:500;line-height:16px;color:var(--ink);margin-left:6px}
.main-nav a{position:absolute;top:26px;font-size:12.5px;color:#666;text-decoration:none;letter-spacing:.3px}
.main-nav a.active{color:var(--ink);border-bottom:1px solid var(--ink);padding-bottom:3px}
.btn{display:flex;align-items:center;justify-content:center;background:var(--green);color:var(--white);font-size:12.5px;font-weight:500;letter-spacing:.4px;text-decoration:none}
.btn-header{position:absolute;left:908px;top:20px;width:158px;height:28px}

/* hero */
.hero{position:absolute;left:0;top:70px;width:1200px;height:491px;background:linear-gradient(180deg,#e0e0e0,#ececec)}
.hero-photo{position:absolute;right:0;top:0;width:780px;height:491px;background:linear-gradient(90deg,rgba(0,0,0,0) 0%,rgba(80,80,80,.12) 45%,rgba(150,150,150,.22) 100%)}
.hero-title{position:absolute;left:134px;top:100px;font-size:44px;font-weight:500;line-height:52px;color:var(--ink);width:660px}
.hero-points{position:absolute;left:134px;top:222px;list-style:none}
.hero-points li{font-size:15.5px;color:#777;height:27px;padding-left:28px;position:relative}
.hero-points svg{position:absolute;left:0;top:3px}
.btn-hero{position:absolute;left:134px;top:323px;width:193px;height:36px;font-size:13px}
.btn-video{position:absolute;left:346px;top:323px;width:192px;height:36px;border:1.5px solid var(--green);color:var(--green);background:transparent;gap:10px}
.hero-note{position:absolute;left:134px;top:370px;font-size:12px;color:var(--muted)}

/* why */
.why{position:absolute;left:0;top:561px;width:1200px;height:588px;background:var(--green);color:var(--white);text-align:center}
.why-title{position:absolute;left:0;top:100px;width:1200px;font-size:32px;font-weight:500}
.why-rule{position:absolute;left:545px;top:143px;width:110px;height:1px;background:var(--white)}
.why-lead{position:absolute;left:0;top:162px;width:1200px;font-size:15.5px;font-weight:500;line-height:28px}
.benefit{position:absolute;top:269px;width:220px;height:195px;background:var(--white);color:var(--ink);padding:30px 18px 0}
.benefit svg{display:block;margin:0 auto}
.benefit h3{font-size:19px;font-weight:400;margin-top:12px}
.benefit p{font-size:11.5px;color:var(--muted);line-height:17px;margin-top:8px}

/* features */
.feature{position:absolute;left:0;width:1200px;height:325px}
.feature-photo{position:absolute;top:0;width:600px;height:325px}
.feature-text{position:absolute;top:0;width:600px;height:325px;padding:0 80px 0 47px;display:flex;flex-direction:column;justify-content:center;background:#fafafa}
.feature-text h2{font-size:28px;font-weight:500;color:var(--ink);margin-bottom:18px}
.feature-text p{font-size:14.5px;color:#858585;line-height:26px;max-width:400px}

/* offer band */
.offer{position:absolute;left:0;top:2124px;width:1200px;height:214px;background:var(--band)}
.offer-figure{position:absolute;left:130px;top:58px;font-size:82px;font-weight:500;color:var(--green);letter-spacing:-1px}
.offer-text{position:absolute;left:354px;top:76px;font-size:25px;font-weight:500;line-height:33px;color:var(--ink)}
.btn-offer{position:absolute;left:872px;top:76px;width:194px;height:36px}
.offer-note{position:absolute;left:964px;top:122px;font-size:12px;color:var(--muted)}
</style>
</head>
<body>

<header class="site-header">
  <div class="brand">
    <span class="brand-square"></span>
    <span class="brand-name">TUVELO</span>
    <span class="brand-tagline">Bløde basics -<br>nemt og ligetil</span>
  </div>
  <nav class="main-nav">
    <a href="#" class="active" style="left:485px">HOME</a>
    <a href="#" style="left:566px">WHY BAMBOO</a>
    <a href="#" style="left:696px">ABOUT US</a>
    <a href="#" style="left:800px">REVIEWS</a>
  </nav>
  <a href="#" class="btn btn-header">BUY NOW</a>
</header>

<section class="hero">
  <div class="hero-photo" role="img" aria-label="Photo of a woman in a grey knit jumper sitting on the floor wearing black knee-high bamboo socks"></div>
  <h1 class="hero-title">Enjoy Your First Pair of Bamboo Socks for Only 20 PKK</h1>
  <ul class="hero-points">
    <li><svg width="16" height="12" viewBox="0 0 16 12"><path d="M1 6l4.5 4.5L15 1" fill="none" stroke="#3bb083" stroke-width="1.8"/></svg>We have been working on textile for more than 10 years</li>
    <li><svg width="16" height="12" viewBox="0 0 16 12"><path d="M1 6l4.5 4.5L15 1" fill="none" stroke="#3bb083" stroke-width="1.8"/></svg>All products meet our high quality standards</li>
    <li><svg width="16" height="12" viewBox="0 0 16 12"><path d="M1 6l4.5 4.5L15 1" fill="none" stroke="#3bb083" stroke-width="1.8"/></svg>Our customers loves us, and we have a 5 stars rating at scorevane.com</li>
  </ul>
  <a href="#" class="btn btn-hero">BUY NOW</a>
  <a href="#" class="btn btn-video"><svg width="10" height="12" viewBox="0 0 10 12"><path d="M0 0l10 6-10 6z" fill="#3bb083"/></svg>WATCH VIDEO</a>
  <p class="hero-note">Shipment included</p>
</section>

<section class="why">
  <h2 class="why-title">Why Bamboo Clothing?</h2>
  <span class="why-rule"></span>
  <p class="why-lead">It was only in 2011 that the Marlowe Institute discovered how you can make fabric<br>from bamboo stems. Now bamboo has the potential to become the textile of the future.</p>

  <div class="benefit" style="left:134px">
    <svg width="40" height="36" viewBox="0 0 40 36"><path d="M13 3l-10 6 4 7 4-2v19h18V14l4 2 4-7-10-6c-1 3-4 5-7 5s-6-2-7-5z" fill="none" stroke="#3bb083" stroke-width="1.8" stroke-linejoin="round"/></svg>
    <h3>Comfortable</h3>
    <p>Bamboo fabric breathes making you comfortable in garments made in this.</p>
  </div>
  <div class="benefit" style="left:372px">
    <svg width="38" height="38" viewBox="0 0 38 38"><circle cx="19" cy="19" r="16" fill="none" stroke="#3bb083" stroke-width="1.8"/><path d="M12 26c0-9 6-14 15-14 0 9-5 15-15 14zM12 26l8-8" fill="none" stroke="#3bb083" stroke-width="1.8"/></svg>
    <h3>Eco-friendly</h3>
    <p>Bamboo is a very fast-growing, tropical forest product, which does not require the use of pesticides</p>
  </div>
  <div class="benefit" style="left:609px">
    <svg width="38" height="38" viewBox="0 0 38 38"><path d="M12 5l-8 5 3 6 3-1v18h18V15l3 1 3-6-8-5h-14z" fill="none" stroke="#3bb083" stroke-width="1.8" stroke-linejoin="round"/><path d="M15 5c1 3 3 4 4 4s3-1 4-4" fill="none" stroke="#3bb083" stroke-width="1.8"/></svg>
    <h3>Exquistely soft</h3>
    <p>The moment you wear it next to your skin you will notice the difference between other fabrics.</p>
  </div>
  <div class="benefit" style="left:846px">
    <svg width="36" height="38" viewBox="0 0 36 38"><circle cx="18" cy="5" r="3" fill="none" stroke="#3bb083" stroke-width="1.8"/><path d="M5 26c0-10 6-17 13-17s13 7 13 17" fill="none" stroke="#3bb083" stroke-width="1.8"/><rect x="3" y="26" width="30" height="8" fill="none" stroke="#3bb083" stroke-width="1.8"/><path d="M9 18h18M7 22h22" stroke="#3bb083" stroke-width="1.5"/></svg>
    <h3>Thermo-control</h3>
    <p>Bamboo fabric is warm, thanks to its hollow microfibre, yet is also breathable.</p>
  </div>
</section>

<section class="feature" style="top:1149px">
  <div class="feature-photo" style="left:0;background:linear-gradient(135deg,#d9dde0,#c7ccd1 55%,#aeb3b8)" role="img" aria-label="Photo of legs in black over-knee socks holding pink shopping bags in a bright mall"></div>
  <div class="feature-text" style="left:600px">
    <h2>Completely Clean</h2>
    <p>Bamboo fibers doesnot under go much chemical processing to make the fabric ; so you can easily wear it without causing any allergic irritation to the skin that is more prevalent with heavily processes fabrics.</p>
  </div>
</section>

<section class="feature" style="top:1473px">
  <div class="feature-text" style="left:0;padding-left:134px;padding-right:40px">
    <h2>Strong Material</h2>
    <p>Bamboo fabric is lightweight yet strong. The natural processing of verdanex bamboo allows the fibre to remain strong to produce an extremely high quality product. This process gives a material that is very durable.</p>
  </div>
  <div class="feature-photo" style="left:600px;background:linear-gradient(160deg,#4a5564,#2f3640 55%,#6c737c)" role="img" aria-label="Photo of a man's legs in dark socks and black leather shoes beside a bed"></div>
</section>

<section class="feature" style="top:1798px">
  <div class="feature-photo" style="left:0;background:linear-gradient(135deg,#f2f3f4,#dfe2e4 60%,#b9bcbf)" role="img" aria-label="Photo of a woman in a black dress and knee-high socks sitting in a white glass walkway"></div>
  <div class="feature-text" style="left:600px">
    <h2>Water Absorbent</h2>
    <p>Bamboo fibers are water absobent. So if you live in a humid environment this is the fabric for you. Think of the sweat it will absorb and evaporate out of your body.</p>
  </div>
</section>

<section class="offer">
  <div class="offer-figure">-90%</div>
  <p class="offer-text">Get Your First Pair of Socks With<br>an Exclusive Discount</p>
  <a href="#" class="btn btn-offer">BUY NOW</a>
  <p class="offer-note">Shipment included</p>
</section>

</body>
</html>
```